Brand new letterhead, business card, email signature etc.

We are a financial company in London, UK. Our website is www.marlowvane.com. We're wanting a complete remodel of the company colours, letter head, business cards, email signatures, etc. Looking to keep the same font for the company name. I have upload a colour palette that we want to work with. We're looking for company letterhead for outgoing letters/ correspondence, letterhead for internal documentation, email signatures, e-letters. etc. Ultimately we will redesign the entire website also. It is important that our clients get a strong, secure, warm, trustworthy, solid feeling and first impression.
Updates

Designs look the same

Target Market(s)

Institutional investors, (ultra) high net worth individuals

Industry/Entity Type

Finance, Invesments banking.

Font styles to use
Other font styles liked:
• Current font is "Champagne & Limousines"

Requirements
Must have
• Must use the colours provided on the PDF uploaded to the portal. The purple = main colour. The red = accent colour.
Nice to have
• Nice to use same font as now for the company name "Corvane". Font is "Champagne & Limousines". Nice to have some reference to the old logo flower, but only subtle.
Should not have
• Do not use the colour red from our website. Use the colours provided on the colour palette PDF that I uploaded in the portal.

```html
<!DOCTYPE html>
<html lang="en">
<head>
<meta charset="utf-8">
<title>Corvane Business Card</title>
<link href="https://fonts.googleapis.com/css2?family=Roboto:ital,wght@0,300;0,400;0,700;1,700&display=swap" rel="stylesheet">
<style>
  :root {
    --stage: #141217;
    --purple-main: #3a2a4d;
    --purple-deep: #2a1f38;
    --purple-light: #4a3862;
    --ink: #f4f2f7;
    --ink-soft: #d3cdde;
    --rule: #8f84a0;
    --accent: #c8102e;
    --edge-white: #f4f4f4;
  }
  * { margin: 0; padding: 0; box-sizing: border-box; }
  html, body {
    width: 1200px; height: 963px; overflow: hidden;
    background: var(--stage);
    font-family: "Roboto", Arial, sans-serif;
    color: var(--ink);
  }
  .canvas { position: relative; width: 1200px; height: 963px; }

  .card {
    position: absolute;
    width: 620px; height: 354px;
    background: linear-gradient(160deg, var(--purple-main), var(--purple-deep));
    overflow: hidden;
    box-shadow: 0 18px 40px rgba(0,0,0,.55);
  }
  .card--front { left: 70px; top: 90px; }
  .card--back { left: 510px; top: 520px; }

  /* brand lockup */
  .brand { position: absolute; display: flex; align-items: center; }
  .brand__mark { display: block; border: 1.5px solid var(--ink); }
  .brand__name {
    font-weight: 300; text-transform: uppercase; color: var(--ink);
    letter-spacing: .22em; line-height: 1;
  }
  .card--front .brand { left: 40px; top: 34px; gap: 16px; }
  .card--front .brand__mark { width: 58px; height: 58px; }
  .card--front .brand__name { font-size: 40px; }

  .faint-emblem {
    position: absolute; right: 40px; bottom: 20px;
    width: 280px; height: 240px;
    background: radial-gradient(ellipse at 55% 60%, rgba(255,255,255,.05), rgba(255,255,255,0) 65%);
  }

  /* person */
  .person { position: absolute; right: 44px; top: 138px; text-align: right; }
  .person__name {
    color: var(--accent); font-size: 22px; font-weight: 400;
    letter-spacing: .04em; text-transform: uppercase; line-height: 1.2;
  }
  .person__role { font-size: 15px; font-weight: 300; color: var(--ink); margin-top: 2px; }
  .person-bar {
    position: absolute; right: 0; top: 140px;
    width: 14px; height: 48px; background: var(--accent);
  }

  /* addresses */
  .offices { position: absolute; left: 40px; top: 128px; font-size: 13.5px; line-height: 1.38; }
  .offices__entity { font-weight: 700; font-style: italic; color: var(--ink); }
  .offices__line { font-weight: 300; color: var(--ink-soft); }
  .divider {
    position: absolute; left: 40px; top: 220px;
    width: 330px; height: 1px; background: var(--rule);
  }

  .contacts {
    position: absolute; left: 40px; top: 232px;
    font-size: 14px; font-weight: 300; line-height: 18px;
  }
  .contacts__row { display: flex; align-items: center; gap: 40px; margin-bottom: 6px; }
  .contact { display: flex; align-items: center; gap: 10px; }
  .contact svg { width: 14px; height: 14px; flex: none; }

  /* bottom edge */
  .edge { position: absolute; left: 0; bottom: 0; width: 100%; height: 12px; }

  /* back */
  .pattern {
    position: absolute; inset: 0;
    background: linear-gradient(135deg, var(--purple-deep), var(--purple-light) 50%, var(--purple-deep));
  }
  .card--back .brand { left: 50%; top: 50%; transform: translate(-50%, -50%); gap: 18px; }
  .card--back .brand__mark { width: 70px; height: 70px; }
  .card--back .brand__name { font-size: 48px; }
</style>
</head>
<body>
<main class="canvas">

  <section class="card card--front" aria-label="Business card front">
    <div class="faint-emblem" role="img" aria-label="Faint oversized brand emblem"></div>

    <div class="brand">
      <span class="brand__mark"></span>
      <span class="brand__name">Corvane</span>
    </div>

    <div class="offices">
      <p class="offices__entity">Corvane (IOM) Limited</p>
      <p class="offices__line">Quayside House, Ramsey, Isle of Man, IM8 2RT</p>
      <p class="offices__entity">Corvane Group Limited</p>
      <p class="offices__line">9th Floor, 14 Aldgate Row, London, EC3N 2LP</p>
    </div>
    <div class="divider"></div>

    <div class="contacts">
      <div class="contacts__row">
        <p class="contact">
          <svg viewBox="0 0 16 16" aria-hidden="true"><path d="M4 1.5l2.5 3-1.5 1.8a9 9 0 0 0 4.7 4.7l1.8-1.5 3 2.5-1.6 2.2C8 14.5 1.5 8 1.8 3.1z" fill="var(--accent)"/></svg>
          020-555-0148
        </p>
      </div>
      <div class="contacts__row">
        <p class="contact">
          <svg viewBox="0 0 16 16" aria-hidden="true"><rect x="1.5" y="3.5" width="13" height="9" fill="none" stroke="var(--accent)" stroke-width="1.4"/><path d="M1.5 3.5L8 9l6.5-5.5" fill="none" stroke="var(--accent)" stroke-width="1.4"/></svg>
          info@marlowvane.com
        </p>
        <p class="contact">
          <svg viewBox="0 0 16 16" aria-hidden="true"><circle cx="8" cy="8" r="6.5" fill="none" stroke="var(--accent)" stroke-width="1.4"/><ellipse cx="8" cy="8" rx="2.8" ry="6.5" fill="none" stroke="var(--accent)" stroke-width="1.2"/><path d="M1.5 8h13M2.5 4.8h11M2.5 11.2h11" stroke="var(--accent)" stroke-width="1.1"/></svg>
          www.marlowvane.com
        </p>
      </div>
    </div>

    <div class="person-bar"></div>
    <div class="person">
      <p class="person__name">Daniel Ashford</p>
      <p class="person__role">Manager</p>
    </div>

    <svg class="edge" viewBox="0 0 620 12" preserveAspectRatio="none" aria-hidden="true">
      <polygon points="0,0 390,0 405,12 0,12" fill="var(--accent)"/>
      <polygon points="405,4 620,4 620,12 412,12" fill="var(--edge-white)"/>
    </svg>
  </section>

  <section class="card card--back" aria-label="Business card back">
    <div class="pattern" role="img" aria-label="Tonal repeating floral pattern across the card"></div>
    <div class="brand">
      <span class="brand__mark"></span>
      <span class="brand__name">Corvane</span>
    </div>
  </section>

</main>
</body>
</html>
```